Create an awesome website for a medical clinic

This is a new website for a doctor's office. The site should be clean and modern, easy to navigate.

This is a wellness clinic, we want to help our clients have a healthy, active lifestyle. It should be friendly and inviting, and easy for them to call or schedule an appointment.

The site should be responsive and designed using the attached Bootstrap 3 PSD.

We will provide stock photos, until then please use stock photos from:

pixelharbor.com or
framequarry.com (preferred)

Some example sites of clean and modern designs that we like:

https://tulsaspinecare.com/
http://reachpastjoints.com/
http://turninghealthier.com/

Also attached is a temporary logo you can use.

Reason: Thank you everyone for your great designs - we need a little more time so I'm extending the project.

Need extra days to review

Also, the colors in the new logo I just linked to are the final colors of the logo, so feel free to use any complimentary colors to it.

Hi everyone, The boss wants to change the layout of the site a little bit - here's the revised layout: https://www.filecrate.com/s/k9rt31vx2qp84zn/notes%2011_29_2017.pdf?dl=0 And the graphic assets you can use are here: https://www.filecrate.com/s/k9rt31vx2qp84zn/notes%2011_29_2017.pdf?dl=0 Feel free to change the background color of the "topbar", and change the icons of the "why people trust us" if you want, these are just temporary placeholders. Thanks for your patience and hard work!

Target Market(s)

People seeking medical treatment (wellness clinic)

Industry/Entity Type

Doctor

Number of Pages Required

1 page

Font styles to use
Sans Serif

Colors
0592cd
33a6d7
abd037
9bcb3c

Requirements
Must have
• The home page should have: a strong hero image/slideshow, clinic phone number should be prominent and at the top of the page (in the nav), a "what to expect" section (this is like a FAQs section - see attachment), and a strong call to action (a button to call or schedule an appointment).
• The what to expect section is useful so that prospective clients can determine if we're a good fit for them or not. It's a basic, first-step pre-qualification block of information.
• Social media icons which links to our social media profiles should be included.
Nice to have
• - Link to 3 most recent blog entries
• - Testimonials
• - How a multilevel nav menu looks.

```html
<!DOCTYPE html>
<html lang="en">
<head>
<meta charset="utf-8">
<title>Fernleaf Medical Clinic</title>
<link href="https://fonts.googleapis.com/css2?family=Roboto:wght@400;500;700&family=Open+Sans:ital,wght@0,400;0,600;1,400&display=swap" rel="stylesheet">
<style>
:root{
  --blue:#0592cd;
  --blue-light:#33a6d7;
  --sky:#29a8e0;
  --green:#9bcb3c;
  --green-light:#abd037;
  --ink:#222;
  --text:#555;
  --muted:#888;
  --line:#e2e2e2;
  --pale:#f3f3f3;
  --footer:#161616;
}
*{box-sizing:border-box;margin:0;padding:0}
html,body{width:1200px;height:3346px;overflow:hidden}
body{font-family:"Open Sans",Arial,sans-serif;color:var(--text);background:#fff;position:relative}
a{color:inherit;text-decoration:none}
.section{position:absolute;left:0;width:1200px}
.heading{font-family:"Roboto",Arial,sans-serif;font-weight:500;color:var(--ink);text-transform:uppercase}

/* header */
.site-header{top:0;height:118px;background:#fff;z-index:5}
.brand{position:absolute;left:98px;top:34px;display:flex;align-items:center;gap:12px;font-family:"Open Sans",Arial,sans-serif;font-weight:600;font-size:26px;color:var(--green);line-height:1}
.brand .mark{width:34px;height:34px;border-radius:50%;background:var(--green);flex:none}
.topbar{position:absolute;right:98px;top:17px;display:flex;align-items:center;gap:20px;font-family:"Roboto",sans-serif}
.call{display:flex;align-items:center;gap:10px;font-size:16px;color:#333}
.call svg{width:22px;height:22px}
.btn-appt{background:var(--sky);color:#fff;font-size:14px;font-weight:500;padding:10px 18px;text-transform:uppercase;display:flex;gap:8px;align-items:center}
.main-nav{position:absolute;right:98px;top:68px;display:flex;font-family:"Roboto",sans-serif;font-size:15px;text-transform:uppercase;color:#333}
.main-nav a{padding:14px 11px;height:50px;display:block}
.main-nav a.active{color:var(--green)}
.main-nav a.open{background:var(--sky);color:#fff}

/* dropdown */
.mega{position:absolute;left:570px;top:118px;width:534px;height:245px;background:rgba(255,255,255,.96);border:3px solid var(--sky);border-top:none;z-index:6;display:flex;padding:28px 36px;gap:60px;font-family:"Roboto",sans-serif}
.mega h4{font-size:14px;font-weight:500;color:#444;padding-bottom:12px;border-bottom:1px solid #ccc;margin-bottom:12px;width:180px}
.mega li{list-style:none;font-size:12.5px;color:#555;line-height:26px}
.mega li::before{content:"›";margin-right:8px;color:#888}

/* hero */
.hero{top:118px;height:565px;background:linear-gradient(180deg,#7fa35a 0%,#b7cc8a 30%,#5f8a35 60%,#3f6a1f 100%)}
.hero-text{position:absolute;left:107px;top:185px;color:#fff;font-family:"Roboto",sans-serif}
.hero-text h1{font-size:44px;font-weight:500;line-height:1.08;text-transform:uppercase}
.hero-text p{font-size:17px;font-weight:500;line-height:1.45;margin-top:12px;width:400px}
.btn-ghost{display:inline-flex;gap:8px;align-items:center;margin-top:22px;border:2px solid #fff;padding:9px 15px;font-size:14px;text-transform:uppercase}
.slide-arrow{position:absolute;top:275px;width:34px;height:34px;border-radius:50%;background:rgba(0,0,0,.75);display:flex;align-items:center;justify-content:center}
.slide-arrow.prev{left:48px}.slide-arrow.next{right:48px}

/* welcome */
.welcome{top:683px;height:479px}
.welcome h2{position:absolute;left:97px;top:100px;font-size:38px}
.welcome h2 span{color:var(--green)}
.welcome .copy{position:absolute;left:97px;top:162px;width:480px;font-size:11.5px;line-height:1.75}
.welcome .copy p+p{margin-top:10px}
.btn-outline{position:absolute;left:97px;top:340px;border:1px solid #555;padding:8px 14px;font-size:11.5px;text-transform:uppercase;color:#333}
.video{position:absolute;left:627px;top:86px;width:472px;height:305px;background:linear-gradient(135deg,#8fa8b5,#d4dde2 50%,#6f8796)}
.video .play{position:absolute;left:206px;top:122px;width:60px;height:60px;border-radius:50%;border:4px solid #fff;display:flex;align-items:center;justify-content:center}

/* services */
.services{top:1162px;height:598px;background:linear-gradient(90deg,#e9e9e9,#f4f4f4 20%,#e6e6e6 40%,#f2f2f2 60%,#e8e8e8 80%,#f3f3f3)}
.services .curve{position:absolute;left:0;bottom:0;width:1200px;height:120px}
.section-title{position:absolute;left:0;width:1200px;text-align:center;font-size:32px}
.services .section-title{top:64px}
.title-rule{position:absolute;left:570px;width:60px;height:3px;background:var(--sky)}
.cards{position:absolute;left:98px;top:162px;display:flex;gap:10px}
.card{width:244px;height:266px;color:#fff;text-align:center;padding:22px 20px;font-family:"Roboto",sans-serif}
.card.blue{background:var(--sky)}.card.green{background:var(--green)}
.card:nth-child(4){height:255px}
.card svg{width:48px;height:48px;margin-bottom:16px}
.card h3{font-size:14px;font-weight:500;text-transform:uppercase;line-height:1.4;min-height:40px;padding:0 18px}
.card p{font-size:11.5px;line-height:1.65;margin-top:10px;font-family:"Open Sans",sans-serif}
.card .more{display:block;font-size:11.5px;margin-top:14px;text-transform:uppercase}

/* what to expect */
.expect{top:1760px;height:363px}
.expect .section-title{top:0;font-size:30px}
.faq-row{position:absolute;left:98px;top:78px;display:flex;gap:32px}
.faq{width:313px;border:1px solid var(--line);border-top:none}
.faq-head{display:flex;height:36px;background:var(--green);color:#fff;font-size:13px;font-weight:600;align-items:center}
.faq-head span{flex:1;padding-left:14px}
.faq-head b{width:34px;height:36px;background:#444;display:flex;align-items:center;justify-content:center;font-size:18px}
.faq p{padding:28px 20px 30px;font-size:12px;line-height:1.9}

/* blog */
.blog{top:2123px;height:615px;background:linear-gradient(180deg,#1c8fd0 0%,#2a9fdc 55%,#3aa6dd 100%)}
.blog .section-title{top:68px;color:#fff}
.posts{position:absolute;left:98px;top:155px;display:flex;gap:28px}
.post{width:316px;height:365px;background:#fff;text-align:center;border-radius:6px 6px 0 0;overflow:hidden}
.post .thumb{height:200px;position:relative}
.post .thumb svg{position:absolute;left:0;bottom:0;width:316px;height:40px}
.post h3{font-family:"Roboto",sans-serif;font-size:14px;font-weight:500;color:#333;text-transform:uppercase;margin-top:18px}
.post .meta{font-size:12px;color:var(--blue);font-style:italic;margin-top:10px}
.post .meta span{margin:0 8px}
.post p{font-size:12px;line-height:1.7;padding:10px 22px 0}

/* testimonial */
.testimonial{top:2738px;height:248px;background:#f1f1f1}
.avatar{position:absolute;left:130px;top:55px;width:155px;height:155px;border-radius:50%;border:6px solid var(--sky);background:linear-gradient(180deg,#f1ece6,#d8cbbd)}
.quote{position:absolute;left:333px;top:60px;width:735px;font-size:13px;font-style:italic;line-height:1.9;color:#555}
.quote cite{display:block;margin-top:14px;font-size:15px;color:var(--blue)}
.dots{position:absolute;left:333px;top:190px;display:flex;gap:5px}
.dots i{width:22px;height:3px;background:#ccc}.dots i:first-child{background:var(--sky)}

/* footer */
.site-footer{top:2986px;height:360px;background:var(--footer);color:#ddd;font-family:"Roboto",sans-serif}
.col{position:absolute;top:64px}
.col h4{font-size:18px;font-weight:500;color:#fff;text-transform:uppercase;margin-bottom:22px}
.contact-line{display:flex;gap:14px;font-size:13px;line-height:1.5;margin-bottom:14px;color:#ddd}
.contact-line svg{width:18px;height:18px;flex:none;margin-top:2px}
.links li{list-style:none;font-size:12.5px;line-height:24px}
.col.signup p{font-size:11.5px;line-height:1.6;width:286px}
.field{margin-top:16px;width:286px;height:40px;background:#fff;color:#555;font-size:11.5px;padding:12px}
.btn-sub{margin-top:14px;display:inline-block;background:var(--sky);color:#fff;font-size:12px;padding:12px 14px;text-transform:uppercase}
.social li{list-style:none;display:flex;gap:10px;align-items:center;font-size:13px;margin-bottom:10px}
.social i{width:28px;height:28px;border-radius:50%;border:1px solid #bbb;display:inline-block}
.copyright{position:absolute;left:0;top:322px;width:1200px;text-align:center;font-size:12px;color:#ccc}
</style>
</head>
<body>

<header class="section site-header">
  <a class="brand" href="#"><span class="mark"></span>Fernleaf Medical Clinic</a>
  <div class="topbar">
    <span class="call"><svg viewBox="0 0 24 24"><circle cx="12" cy="12" r="11" fill="none" stroke="#333" stroke-width="1.4"/><path d="M8.5 7.5l2 .2.7 2.3-1.3 1a7 7 0 003.1 3.1l1-1.3 2.3.7.2 2c-4.5.6-8.6-3.5-8-8z" fill="#333"/></svg>Call Us : (555) - 014 - 2210</span>
    <a class="btn-appt" href="#">Schedule an appointment <svg width="14" height="14" viewBox="0 0 14 14"><path d="M1 3h6M1 3v10h10V7M6 8l7-7" stroke="#fff" fill="none" stroke-width="1.5"/></svg></a>
  </div>
  <nav class="main-nav">
    <a class="active" href="#">Home</a><a href="#">About us</a><a class="open" href="#">Services</a><a href="#">What to expect</a><a href="#">Blog</a><a href="#">Testimonials</a><a href="#">Contact</a>
  </nav>
</header>

<div class="mega">
  <div><h4>SERVICES 1</h4><ul><li>Suspendisse dictum nibh</li><li>Duis et mi vitae tortor cursus</li><li>Aliquam quis purus gravida</li><li>Aenean vulputate nunc eget urna</li><li>Vivamus hendrerit ex vitae</li></ul></div>
  <div><h4>SERVICES 1</h4><ul><li>Suspendisse dictum nibh</li><li>Duis et mi vitae tortor cursus</li><li>Aliquam quis purus gravida</li><li>Aenean vulputate nunc eget urna</li><li>Vivamus hendrerit ex vitae</li></ul></div>
</div>

<section class="section hero" role="img" aria-label="Photo of a woman relaxing on sunny green grass outdoors">
  <div class="hero-text">
    <h1>Fernleaf<br>Wellness Clinic</h1>
    <p>Sed ut perspiciatis unde omnis iste natus voluptatem accusantium doloremque laudantium</p>
    <a class="btn-ghost" href="#">Schedule an appointment <svg width="14" height="14" viewBox="0 0 14 14"><path d="M1 3h6M1 3v10h10V7M6 8l7-7" stroke="#fff" fill="none" stroke-width="1.5"/></svg></a>
  </div>
  <a class="slide-arrow prev" href="#"><svg width="12" height="12" viewBox="0 0 12 12"><path d="M8 1L3 6l5 5" stroke="#fff" stroke-width="2.2" fill="none"/></svg></a>
  <a class="slide-arrow next" href="#"><svg width="12" height="12" viewBox="0 0 12 12"><path d="M4 1l5 5-5 5" stroke="#fff" stroke-width="2.2" fill="none"/></svg></a>
</section>

<section class="section welcome">
  <h2 class="heading">Welcome to <span>Fernleaf</span></h2>
  <div class="copy">
    <p>Sed ut perspiciatis unde omnis iste natus error sit voluptatem accusantium doloremque laudantium, totam rem aperiam, eaque ipsa quae ab illo inventore veritatis et quasi architecto beatae vitae dicta sunt explicabo. Nemo enim ipsam voluptatem quia voluptas sit aspernatur aut odit aut fugit, sed quia consequuntur magni dolores eos qui ratione voluptatem sequi nesciunt. Neque porro quisquam est, qui dolorem ipsum quia</p>
    <p>Sed ut perspiciatis unde omnis iste natus error sit voluptatem accusantium dolore laudantium, totam rem aperiam, eaque ipsa quae</p>
  </div>
  <a class="btn-outline" href="#">Read more ›</a>
  <div class="video" role="img" aria-label="Video still of doctors reviewing a patient chart">
    <span class="play"><svg width="20" height="22" viewBox="0 0 20 22"><path d="M3 1l16 10L3 21z" fill="#fff"/></svg></span>
  </div>
</section>

<section class="section services">
  <h2 class="heading section-title">Our Services</h2>
  <span class="title-rule" style="top:118px"></span>
  <div class="cards">
    <div class="card blue">
      <svg viewBox="0 0 48 48"><rect x="14" y="4" width="20" height="32" rx="6" fill="none" stroke="#fff" stroke-width="3"/><rect x="19" y="10" width="10" height="8" fill="#fff"/><path d="M24 36v8" stroke="#fff" stroke-width="3"/></svg>
      <h3>Diagnostic evaluation and treatment</h3>
      <p>Sed ut perspiciatis unde omnis iste natus error sit voluptatem accusantium dolorque laudantium, totam rem aperiam</p>
      <a class="more" href="#">Read more ›</a>
    </div>
    <div class="card green">
      <svg viewBox="0 0 48 48"><circle cx="24" cy="24" r="18" fill="none" stroke="#fff" stroke-width="3"/><path d="M16 24h16M24 16v16" stroke="#fff" stroke-width="3"/></svg>
      <h3>Developmental disabilities</h3>
      <p>Sed ut perspiciatis unde omnis iste natus error sit voluptatem accusantium dolorque laudantium, totam rem aperiam</p>
      <a class="more" href="#">Read more ›</a>
    </div>
    <div class="card blue">
      <svg viewBox="0 0 48 48"><path d="M24 44V22M24 22l-10-10M24 22l10-10M24 30l-8-6M24 30l8-6" stroke="#fff" stroke-width="3" fill="none"/><circle cx="14" cy="10" r="4" fill="#fff"/><circle cx="34" cy="10" r="4" fill="#fff"/><circle cx="24" cy="8" r="4" fill="#fff"/></svg>
      <h3>Early childhood assessments</h3>
      <p>Sed ut perspiciatis unde omnis iste natus error sit voluptatem accusantium dolorque laudantium, totam rem aperiam</p>
      <a class="more" href="#">Read more ›</a>
    </div>
    <div class="card green">
      <svg viewBox="0 0 48 48"><circle cx="24" cy="22" r="16" fill="none" stroke="#fff" stroke-width="3"/><path d="M16 20c4-4 6 4 10 0s6 4 8 0M18 28c4-3 8 3 12 0" stroke="#fff" stroke-width="2.5" fill="none"/></svg>
      <h3>Psychopharmacology</h3>
      <p>Sed ut perspiciatis unde omnis iste natus error sit voluptatem accusantium dolorque laudantium, totam rem aperiam</p>
      <a class="more" href="#">Read more ›</a>
    </div>
  </div>
  <svg class="curve" viewBox="0 0 1200 120" preserveAspectRatio="none"><path d="M0 30Q600 -30 1200 30V120H0z" fill="#fff"/></svg>
</section>

<section class="section expect">
  <h2 class="heading section-title">What to Expect</h2>
  <div class="faq-row">
    <div class="faq"><div class="faq-head"><span>Where does it come from?</span><b>–</b></div><p>Sed ut perspiciatis unde omnis iste natus error sit voluptatem accusantium doloremque laudantium, totam rem aperiam, eaque ipsa quae ab illo inventore veritatis et quasi architecto beatae vitae dicta sunt explicabo.</p></div>
    <div class="faq"><div class="faq-head"><span>Where does it come from?</span><b>–</b></div><p>Sed ut perspiciatis unde omnis iste natus error sit voluptatem accusantium doloremque laudantium, totam rem aperiam, eaque ipsa quae ab illo inventore veritatis et quasi architecto beatae vitae dicta sunt explicabo.</p></div>
    <div class="faq"><div class="faq-head"><span>Where does it come from?</span><b>–</b></div><p>Sed ut perspiciatis unde omnis iste natus error sit voluptatem accusantium doloremque laudantium, totam rem aperiam, eaque ipsa quae ab illo inventore veritatis et quasi architecto beatae vitae dicta sunt explicabo.</p></div>
  </div>
</section>

<section class="section blog">
  <h2 class="heading section-title">Recent Blog</h2>
  <div class="posts">
    <article class="post">
      <div class="thumb" role="img" aria-label="Word cloud image about health and nutrition" style="background:linear-gradient(135deg,#1d3a5a,#4f7a9a 60%,#2b4e6c)"><svg viewBox="0 0 316 40" preserveAspectRatio="none"><path d="M0 40V10Q158 55 316 10V40z" fill="#fff"/></svg></div>
      <h3>Sed ut perspiciatis unde</h3>
      <div class="meta">◷ July 05, 2017<span>|</span>0 Comments</div>
      <p>Nemo enim ipsam voluptatem quia voluptas sit atur aut odit aut fugit, sed quia consequuntur magni dolores eos qui ratione voluptatem</p>
    </article>
    <article class="post">
      <div class="thumb" role="img" aria-label="Photo of a woman stretching her arms in a green park" style="background:linear-gradient(180deg,#cfe6a0,#8dbb4a 60%,#5f8f2c)"><svg viewBox="0 0 316 40" preserveAspectRatio="none"><path d="M0 40V10Q158 55 316 10V40z" fill="#fff"/></svg></div>
      <h3>Sed ut perspiciatis unde</h3>
      <div class="meta">◷ July 05, 2017<span>|</span>0 Comments</div>
      <p>Nemo enim ipsam voluptatem quia voluptas sit atur aut odit aut fugit, sed quia consequuntur magni dolores eos qui ratione voluptatem</p>
    </article>
    <article class="post">
      <div class="thumb" role="img" aria-label="Photo of two people stretching on an outdoor sports court" style="background:linear-gradient(180deg,#2f6fa8,#4e8fc0 55%,#3a6f8f)"><svg viewBox="0 0 316 40" preserveAspectRatio="none"><path d="M0 40V10Q158 55 316 10V40z" fill="#fff"/></svg></div>
      <h3>Sed ut perspiciatis unde</h3>
      <div class="meta">◷ July 05, 2017<span>|</span>0 Comments</div>
      <p>Nemo enim ipsam voluptatem quia voluptas sit atur aut odit aut fugit, sed quia consequuntur magni dolores eos qui ratione voluptatem</p>
    </article>
  </div>
</section>

<section class="section testimonial">
  <div class="avatar" role="img" aria-label="Portrait photo of a smiling client"></div>
  <blockquote class="quote">“ Sed ut perspiciatis unde omnis iste natus error sit voluptatem accusantium doloremque laudantium, totam rem aperiam, eaque ipsa quae ab illo inventore veritatis et quasi architecto beatae vitae dicta sunt explicabo. Nemo enim ipsam voluptatem quia voluptas sit aspernatur aut odit aut fugit, sed quia consequuntur<cite>Jane Harlow - Fernleaf Medical Clinic</cite></blockquote>
  <div class="dots"><i></i><i></i><i></i></div>
</section>

<footer class="section site-footer">
  <div class="col" style="left:98px;width:300px">
    <h4>Contact us</h4>
    <div class="contact-line"><svg viewBox="0 0 18 18"><path d="M9 1a5 5 0 015 5c0 4-5 11-5 11S4 10 4 6a5 5 0 015-5z" fill="none" stroke="#ddd" stroke-width="1.4"/><circle cx="9" cy="6" r="1.8" fill="#ddd"/></svg><span>Fernleaf Medical Clinic<br>1820 Alder Lane Suite 110<br>Riverton Colorado 80099</span></div>
    <div class="contact-line"><svg viewBox="0 0 18 18"><path d="M3 2l3 .3 1 3.2-1.8 1.3a9 9 0 004.5 4.5L11 9.5l3.2 1 .3 3C8 15 1.5 8.5 3 2z" fill="none" stroke="#ddd" stroke-width="1.4"/></svg><span>Phone : +1 555 019 4471</span></div>
    <div class="contact-line"><svg viewBox="0 0 18 18"><rect x="1.5" y="4" width="15" height="10" fill="none" stroke="#ddd" stroke-width="1.4"/><path d="M1.5 4l7.5 6 7.5-6" fill="none" stroke="#ddd" stroke-width="1.4"/></svg><span>support@fernleafclinic.com</span></div>
  </div>
  <div class="col" style="left:458px">
    <h4 style="font-size:15px">Quick links</h4>
    <ul class="links"><li>Home</li><li>About Us</li><li>What to expect</li><li>Services</li><li>Blog</li><li>Contacts</li></ul>
  </div>
  <div class="col signup" style="left:651px">
    <h4>Sign up to receive email</h4>
    <p>Excepteur sint occaecat cupidatat non proident, sunt in culpa qui Nemo enim ipsam voluptatem</p>
    <div class="field">Enter Name</div>
    <a class="btn-sub" href="#">Subscribe</a>
  </div>
  <div class="col" style="left:1002px">
    <h4 style="font-size:15px">Social media</h4>
    <ul class="social"><li><i></i>Community</li><li><i></i>Updates</li><li><i></i>Circles</li><li><i></i>Videos</li></ul>
  </div>
  <p class="copyright">Copyright © Fernleaf Medical Clinic 2017. All rights reserved.</p>
</footer>

</body>
</html>
```